High-end construction company needs a business card design

We need a modern looking business card that draws people in, is memorable and looks so good people will want to sick it on their fridges.
On the first side what is needed are:
Logo
My name - Tomasz Brelwik
Title - Managing Director
Website - www.varkelt.co.uk
Email - tomasz@varkelt.co.uk
Telephone - 020 5194 6281
Mobile - 07845139072
On the back side was is needed is a list of all the services we provide:
-Kitchen Renovations
-Bathroom Renovations
-House Renovations
-Garage Conversions
-Extensions
-Loft Conversions
-Conservatories
-Carpentry
-Tiling
-Electrical
-Plumbing & Heating
-Bricklaying
-Landscaping
-Decorating
-Plastering
We would like the colours to be the same shades as on the logo with grey or black for the words.
Target Market(s)
Anyone who needs building work done
Contact Information for Business Card
This business card is for a construction company which strives to deliver excellent service and quality.
The look and feel of the card should represent this.
Requirements
Must have
- On the first side what is needed are:
Logo
My name - Tomasz Brelwik
Title - Managing Director
Website - www.varkelt.co.uk
Email - tomasz@varkelt.co.uk
Telephone - 020 5194 6281
Mobile - 07845139072
Nice to have
- Cool looking features

```html
<!DOCTYPE html>
<html lang="en">
<head>
<meta charset="utf-8">
<title>Varkelt Construction Ltd – Business Card</title>
<link rel="stylesheet" href="https://fonts.googleapis.com/css2?family=Michroma&family=Montserrat:wght@400;500;700;800&display=swap">
<style>
  :root {
    --green-light: #7cc242;
    --green-mid: #5fa83a;
    --green-deep: #4a9234;
    --green-logo: #5fae3e;
    --green-band: #5aa33a;
    --white: #ffffff;
    --page: #2a2a2a;
  }
  * { box-sizing: border-box; margin: 0; padding: 0; }
  html, body { width: 1200px; height: 880px; overflow: hidden; }
  body {
    background: var(--page);
    position: relative;
    font-family: "Montserrat", sans-serif;
  }
  .card {
    position: absolute;
    left: 250px;
    width: 700px;
    height: 400px;
    border-radius: 26px;
    overflow: hidden;
    box-shadow: 0 10px 30px rgba(0,0,0,0.45);
  }
  .card--services { top: 28px; background: linear-gradient(135deg, var(--green-light) 0%, var(--green-mid) 60%, var(--green-deep) 100%); }
  .card--contact { top: 452px; background: var(--white); }

  /* services side */
  .service-list {
    position: absolute;
    left: 46px;
    top: 50px;
    list-style: none;
    font-family: "Michroma", sans-serif;
    font-size: 13.5px;
    line-height: 19.6px;
    color: var(--white);
  }
  .service-list li { position: relative; padding-left: 20px; }
  .service-list li::before {
    content: "";
    position: absolute;
    left: 0; top: 6px;
    width: 8px; height: 8px;
    border-radius: 50%;
    background: var(--white);
  }
  .brand-name {
    position: absolute;
    font-family: "Michroma", sans-serif;
    text-transform: uppercase;
    text-align: center;
    white-space: nowrap;
  }
  .brand-name__main { display: block; font-size: 48px; line-height: 1; letter-spacing: 2px; }
  .brand-name__sub { display: block; font-size: 14.5px; letter-spacing: 2.4px; margin-top: 8px; }
  .card--services .brand-name { right: 46px; top: 110px; color: var(--white); }
  .website {
    position: absolute;
    right: 46px;
    bottom: 44px;
    font-family: "Michroma", sans-serif;
    font-size: 14px;
    color: var(--white);
  }

  /* contact side */
  .contact-shape { position: absolute; inset: 0; width: 700px; height: 400px; }
  .card--contact .brand-name { left: 36px; top: 160px; color: var(--green-logo); }
  .card--contact .brand-name__main { font-size: 42px; letter-spacing: 1.5px; }
  .card--contact .brand-name__sub { font-size: 12.5px; letter-spacing: 2px; }
  .person {
    position: absolute;
    left: 470px;
    top: 62px;
    color: var(--white);
  }
  .person__name { font-weight: 800; font-size: 21px; text-transform: uppercase; letter-spacing: 0.5px; }
  .person__title { font-weight: 400; font-size: 14px; margin-top: 2px; }
  .contact-list {
    position: absolute;
    left: 470px;
    top: 176px;
    list-style: none;
    color: var(--white);
    font-size: 14px;
    line-height: 25px;
  }
  .contact-list li { display: flex; align-items: center; gap: 9px; }
  .contact-list svg { width: 17px; height: 17px; flex: none; }
</style>
</head>
<body>

<section class="card card--services">
  <ul class="service-list">
    <li>Kitchen Renovations</li>
    <li>Bathroom Renovations</li>
    <li>House Renovations</li>
    <li>Garage Conversions</li>
    <li>Extensions</li>
    <li>Loft Conversions</li>
    <li>Conservatories</li>
    <li>Carpentry</li>
    <li>Tiling</li>
    <li>Electrical</li>
    <li>Plumbing &amp; Heating</li>
    <li>Bricklaying</li>
    <li>Landscaping</li>
    <li>Decorating</li>
    <li>Plastering</li>
  </ul>
  <div class="brand-name">
    <span class="brand-name__main">Varkelt</span>
    <span class="brand-name__sub">Construction Ltd</span>
  </div>
  <div class="website">www.varkelt.co.uk</div>
</section>

<section class="card card--contact">
  <svg class="contact-shape" viewBox="0 0 700 400" aria-hidden="true">
    <path d="M250 0 C 400 50 420 260 355 400 L 380 400 C 460 250 430 40 250 0 Z" fill="#7cc242"/>
    <path d="M250 0 C 430 40 460 250 380 400 L 700 400 L 700 0 Z" fill="#5aa33a"/>
  </svg>
  <div class="brand-name">
    <span class="brand-name__main">Varkelt</span>
    <span class="brand-name__sub">Construction Ltd</span>
  </div>
  <div class="person">
    <div class="person__name">Tomasz Brelwik</div>
    <div class="person__title">Managing Director</div>
  </div>
  <ul class="contact-list">
    <li>
      <svg viewBox="0 0 20 20" aria-hidden="true"><circle cx="10" cy="10" r="9" fill="none" stroke="#fff" stroke-width="1.6"/><path d="M7 5.5l1.6 2.6-1 1.2c.7 1.4 1.7 2.4 3.1 3.1l1.2-1 2.6 1.6-.6 1.6c-3.6.2-7.6-3.8-7.4-7.4z" fill="#fff"/></svg>
      020 5194 6281
    </li>
    <li>
      <svg viewBox="0 0 20 20" aria-hidden="true"><circle cx="10" cy="10" r="9" fill="none" stroke="#fff" stroke-width="1.6"/><rect x="7" y="5" width="6" height="10" rx="1.2" fill="none" stroke="#fff" stroke-width="1.4"/><circle cx="10" cy="13" r=".8" fill="#fff"/></svg>
      07845139072
    </li>
    <li>
      <svg viewBox="0 0 20 20" aria-hidden="true"><circle cx="10" cy="10" r="9" fill="none" stroke="#fff" stroke-width="1.6"/><rect x="5.5" y="6.5" width="9" height="7" fill="none" stroke="#fff" stroke-width="1.3"/><path d="M5.5 6.5l4.5 4 4.5-4" fill="none" stroke="#fff" stroke-width="1.3"/></svg>
      tomasz@varkelt.co.uk
    </li>
    <li>
      <svg viewBox="0 0 20 20" aria-hidden="true"><circle cx="10" cy="10" r="9" fill="none" stroke="#fff" stroke-width="1.6"/><circle cx="10" cy="10" r="5" fill="none" stroke="#fff" stroke-width="1.2"/><ellipse cx="10" cy="10" rx="2.2" ry="5" fill="none" stroke="#fff" stroke-width="1"/><path d="M5 10h10" stroke="#fff" stroke-width="1"/></svg>
      www.varkelt.co.uk
    </li>
  </ul>
</section>

</body>
</html>
```